Meridale Partners Website

Meridale Partners (MP) provide Analytics & Enterprise Performance Management (EPM) advisory & consultancy services. We are passionate about data and making a difference for our clients by working in partnership with them, helping them on their journey to becoming an Meridale Partner. We deliver insights which give our clients a competitive edge and a much deeper understanding of their organisation.

We need a website which shows who we are, what we do and how we do it.

www.meridale-partners.example is our very basic website at the moment. We want to completely revamp it with a corporate look

```html
<!DOCTYPE html>
<html lang="en">
<head>
<meta charset="utf-8">
<title>Meridale Partners</title>
<link href="https://fonts.googleapis.com/css2?family=Montserrat:wght@600;700&family=Poppins:wght@400;500;600&display=swap" rel="stylesheet">
<style>
:root{
  --navy:#284a61;
  --navy-deep:#1c3547;
  --orange:#e8873a;
  --cream:#fcf6f1;
  --text:#5b5b5b;
  --white:#ffffff;
}
*{box-sizing:border-box;margin:0;padding:0}
html,body{width:1200px;height:3800px;overflow:hidden}
body{position:relative;background:var(--white);font-family:'Poppins',sans-serif;color:var(--text)}
.backdrop{position:absolute;left:0;top:0}
.abs{position:absolute}
.heading{font-family:'Montserrat',sans-serif;font-weight:700;color:var(--navy);text-transform:uppercase;letter-spacing:.5px}
.eyebrow{font-size:15px;color:var(--orange);text-transform:uppercase;letter-spacing:.5px}
.btn{position:absolute;display:flex;align-items:center;height:40px;border-radius:20px;background:var(--orange);color:var(--white);font-family:'Montserrat',sans-serif;font-weight:700;font-size:15px;letter-spacing:.5px;padding:0 22px 0 52px;white-space:nowrap}
.btn .dot{position:absolute;left:0;top:0;width:40px;height:40px;border-radius:50%;background:var(--white);border:2px solid var(--navy);display:flex;align-items:center;justify-content:center}
.brand{display:flex;align-items:center;gap:12px;font-family:'Montserrat',sans-serif;font-weight:700;line-height:1.05;text-transform:uppercase}
.brand .mark{border-radius:50%;border:5px solid currentColor}
/* header */
.site-header .brand{position:absolute;left:60px;top:14px;color:var(--navy);font-size:18px}
.site-header .brand .mark{width:46px;height:46px}
.nav{position:absolute;top:21px;left:629px;display:flex;align-items:center;gap:20px;font-size:13px;color:var(--navy-deep);white-space:nowrap}
.nav .active{border:1.5px solid var(--orange);color:var(--orange);border-radius:16px;padding:6px 14px}
.phone-pill{position:absolute;left:965px;top:13px;width:175px;height:42px;border-radius:21px;background:var(--orange);color:var(--white);font-weight:600;font-size:18px;display:flex;align-items:center;padding-left:52px;white-space:nowrap}
.phone-pill .icon{position:absolute;left:-2px;top:0;width:42px;height:42px;border-radius:50%;background:var(--navy);display:flex;align-items:center;justify-content:center}
/* hero */
.hero-title{position:absolute;left:58px;top:148px;font-family:'Montserrat',sans-serif;font-weight:700;font-size:58px;line-height:1.03;color:var(--white)}
.hero-text{position:absolute;left:60px;top:278px;width:460px;font-size:13.5px;line-height:22px;color:var(--white)}
.slider-arrow{position:absolute;left:1098px;width:42px;height:42px;border-radius:50%;background:rgba(20,40,60,.55);display:flex;align-items:center;justify-content:center}
/* about */
.about-copy{position:absolute;left:163px;top:966px;width:380px;font-size:12px;line-height:24px}
.about-copy p+p{margin-top:22px}
/* services */
.service-card{position:absolute;top:1480px;width:262px;height:311px;background:var(--white);border-radius:0 6px 6px 0;border-left:2px solid var(--orange);box-shadow:0 4px 14px rgba(0,0,0,.06);overflow:hidden}
.service-card .photo{height:168px}
.service-card h3{font-family:'Montserrat',sans-serif;font-weight:700;font-size:15.5px;color:var(--navy);margin:26px 0 0 18px;text-transform:uppercase}
.service-card p{font-size:11.5px;line-height:20px;margin:10px 18px 0 18px}
.read-more{display:flex;align-items:center;gap:6px;font-size:12px;color:var(--orange)}
.read-more .ring{width:16px;height:16px;border:1.3px solid var(--orange);border-radius:50%;display:flex;align-items:center;justify-content:center}
.service-card .read-more{margin:18px 0 0 18px}
/* how */
.how-heading{position:absolute;left:60px;top:2200px;width:540px;font-family:'Montserrat',sans-serif;font-weight:700;font-size:23px;line-height:30px;color:var(--white)}
/* insight */
.insight-card{position:absolute;top:2618px;width:284px;height:342px;border-radius:8px;background:var(--white);box-shadow:0 3px 14px rgba(0,0,0,.08);overflow:hidden}
.insight-card .photo{height:189px}
.insight-card .meta{padding:18px 0 0 20px}
.insight-card time{font-size:11.5px;color:var(--text)}
.insight-card h4{font-family:'Montserrat',sans-serif;font-weight:700;font-size:16px;line-height:22px;color:var(--navy);margin-top:8px}
.insight-card .read-more{margin-top:24px}
.insight-card.featured{background:linear-gradient(160deg,#3a4d5e,#161e27 60%,#0c1117)}
.insight-card.featured .meta{position:absolute;left:0;top:200px}
.insight-card.featured time,.insight-card.featured h4{color:var(--white)}
.insight-card.featured .read-more{margin-top:12px}
/* contact */
.contact-heading{position:absolute;left:128px;top:3205px;font-size:35px;line-height:40px}
/* footer */
.site-footer{color:var(--white)}
.site-footer .brand{position:absolute;left:59px;top:3580px;font-size:21px;color:var(--white)}
.site-footer .brand .mark{width:58px;height:58px}
.partner-badge{position:absolute;left:92px;top:3654px;width:170px;height:28px;display:flex;gap:10px;align-items:center}
.partner-badge span{display:block;height:18px;border-radius:3px}
.foot-col{position:absolute;top:3568px}
.foot-col h5{font-family:'Montserrat',sans-serif;font-weight:700;font-size:15px;margin-bottom:16px;text-transform:uppercase}
.foot-col ul{list-style:none;font-size:11.5px}
.foot-col li{height:26.5px;display:flex;align-items:center;gap:12px}
.foot-col li.bullet::before{content:"";width:5px;height:5px;border-radius:50%;background:var(--orange)}
.contact-list li{align-items:flex-start;height:auto;margin-bottom:14px;line-height:21px}
.social{display:flex;gap:9px}
.social span{width:38px;height:38px;border-radius:50%;background:var(--orange)}
.foot-rule{position:absolute;left:0;top:3751px;width:1200px;height:1px;background:rgba(255,255,255,.25)}
.copyright{position:absolute;left:0;top:3767px;width:1200px;text-align:center;font-size:11px;color:var(--white)}
</style>
</head>
<body>

<svg class="backdrop" width="1200" height="3800" viewBox="0 0 1200 3800" aria-hidden="true">
  <defs>
    <linearGradient id="heroTone" x1="0" y1="0" x2="1" y2="1">
      <stop offset="0" stop-color="#1f3344"/>
      <stop offset=".45" stop-color="#4d6f8e"/>
      <stop offset="1" stop-color="#9fb6cc"/>
    </linearGradient>
    <linearGradient id="cityTone" x1="0" y1="0" x2="1" y2="0">
      <stop offset="0" stop-color="#2a4d66"/>
      <stop offset=".55" stop-color="#1b3046"/>
      <stop offset="1" stop-color="#0f1c2d"/>
    </linearGradient>
  </defs>
  <rect x="0" y="75" width="1200" height="660" fill="url(#heroTone)"/>
  <path d="M0,490 C150,470 300,520 420,600 C520,670 600,720 720,712 C880,700 1020,640 1200,588 L1200,740 L0,740 Z" fill="var(--white)"/>
  <path d="M0,490 C150,470 300,520 420,600 C520,670 600,720 720,712 C880,700 1020,640 1200,588" fill="none" stroke="var(--navy)" stroke-width="4"/>
  <path d="M0,1345 C300,1360 450,1410 700,1395 C950,1380 1100,1320 1200,1290 L1200,2300 L0,2300 Z" fill="var(--cream)"/>
  <path d="M0,2075 C250,2060 500,1960 700,1880 C900,1800 1060,1830 1200,2040 L1200,2555 C1050,2600 950,2490 850,2420 C700,2340 600,2380 450,2420 C300,2470 100,2480 0,2310 Z" fill="url(#cityTone)" role="img" aria-label="Photo of a consultant with a tablet beside a glass wall overlooking a city at night"/>
  <path d="M0,3050 C300,3000 500,3130 750,3090 C950,3060 1100,3010 1200,3020 L1200,3420 L0,3420 Z" fill="var(--cream)"/>
  <path d="M0,3360 C200,3380 400,3510 620,3490 C820,3470 1000,3360 1200,3350" fill="none" stroke="var(--orange)" stroke-width="2"/>
  <path d="M0,3380 C200,3400 400,3530 620,3510 C820,3490 1000,3380 1200,3370 L1200,3800 L0,3800 Z" fill="var(--navy)"/>
</svg>

<header class="site-header">
  <div class="brand"><span class="mark"></span><span>Meridale<br>Partners</span></div>
  <nav class="nav"><span class="active">Home</span><span>Services</span><span>About Us</span><span>Contact Us</span></nav>
  <div class="phone-pill"><span class="icon"><svg width="20" height="20" viewBox="0 0 24 24"><path d="M6.6 10.8a15 15 0 0 0 6.6 6.6l2.2-2.2c.3-.3.7-.4 1-.2 1.1.4 2.3.6 3.6.6.6 0 1 .4 1 1V20c0 .6-.4 1-1 1A17 17 0 0 1 3 4c0-.6.4-1 1-1h3.5c.6 0 1 .4 1 1 0 1.3.2 2.5.6 3.6.1.3 0 .7-.2 1z" fill="#fff"/></svg></span>01 555 0142</div>
</header>

<section class="hero">
  <div class="abs" role="img" aria-label="Photo of a team reviewing analytics charts on a large wall display" style="left:0;top:75px;width:1200px;height:10px"></div>
  <h1 class="hero-title">Meridale<br>Partners</h1>
  <p class="hero-text">We are passionate about data and making a difference for our clients by working in partnership with them, helping them on their Journey to becoming an Meridale Partner</p>
  <div class="btn" style="left:60px;top:360px">CONTACT US<span class="dot"></span></div>
  <div class="slider-arrow" style="top:298px"><svg width="14" height="20"><path d="M3 2l8 8-8 8" stroke="#e8873a" stroke-width="2" fill="none"/></svg></div>
  <div class="slider-arrow" style="top:345px"><svg width="14" height="20"><path d="M11 2l-8 8 8 8" stroke="#e8873a" stroke-width="2" fill="none"/></svg></div>
</section>

<section class="about">
  <div class="eyebrow abs" style="left:0;top:786px;width:1200px;text-align:center">Who we are</div>
  <h2 class="heading abs" style="left:0;top:815px;width:1200px;text-align:center;font-size:33px;line-height:38px">Meridale<br>Partners</h2>
  <div class="about-copy">
    <p>MP are a Data Analytics &amp; EPM company, specialising in the implementation and support of Business Intelligence, EPM and Data Analytics business solutions, both in the Cloud and on-premise</p>
    <p>Meridale Partners is an exciting start-up in the Data Analytics and EPM space. Founded in 2019, MP specialise in the implementation and support of BI, EPM and Data Analytics business solutions, both in the Cloud and on-premise.</p>
  </div>
  <div class="btn" style="left:166px;top:1197px">LEARN MORE<span class="dot"></span></div>
  <div class="abs" role="img" aria-label="Circular photo of a woman working at a laptop" style="left:600px;top:906px;width:456px;height:406px;border-radius:50%;background:radial-gradient(circle at 55% 45%,#d9d2c8,#8fa2b0 55%,#284a61)"></div>
</section>

<section class="services">
  <div class="eyebrow abs" style="left:62px;top:1601px">What we do</div>
  <h2 class="heading abs" style="left:61px;top:1630px;font-size:34px;line-height:38px">Our<br>Services</h2>
  <article class="service-card" style="left:408px">
    <div class="photo" role="img" aria-label="Photo of two colleagues reviewing work on a laptop" style="background:linear-gradient(135deg,#cfc7bd,#6b7480)"></div>
    <h3>Advise &amp; Architect</h3>
    <p>Helping our customers understand the art of the possible.</p>
    <div class="read-more">Read More<span class="ring"><svg width="6" height="8"><path d="M1 1l3 3-3 3" stroke="#e8873a" fill="none"/></svg></span></div>
  </article>
  <article class="service-card" style="left:693px">
    <div class="photo" role="img" aria-label="Photo of a team planning with sticky notes on a glass wall" style="background:linear-gradient(135deg,#a7b1b8,#e3d9c4)"></div>
    <h3>Design &amp; Implement</h3>
    <p>Helping our customers understand the art of the possible.</p>
    <div class="read-more">Read More<span class="ring"><svg width="6" height="8"><path d="M1 1l3 3-3 3" stroke="#e8873a" fill="none"/></svg></span></div>
  </article>
  <article class="service-card" style="left:979px">
    <div class="photo" role="img" aria-label="Photo of a laptop showing analytics dashboards" style="background:linear-gradient(135deg,#c9d4dc,#7f93a6)"></div>
    <h3>Optimse &amp; Manage</h3>
    <p>Helping our customers understand the art of the possible.</p>
    <div class="read-more">Read More<span class="ring"><svg width="6" height="8"><path d="M1 1l3 3-3 3" stroke="#e8873a" fill="none"/></svg></span></div>
  </article>
</section>

<section class="how">
  <div class="eyebrow abs" style="left:61px;top:2160px">How we do it</div>
  <h2 class="how-heading">We Provide Analytics &amp; Enterprise Performance Management (EPM) Advisory &amp; Consultancy Services</h2>
  <div class="btn" style="left:60px;top:2290px">VIEW INSIGHT<span class="dot"></span></div>
</section>

<section class="insight">
  <div class="eyebrow abs" style="left:0;top:2510px;width:1200px;text-align:center">Stay up to date</div>
  <h2 class="heading abs" style="left:0;top:2538px;width:1200px;text-align:center;font-size:34px">Latest Insight</h2>
  <article class="insight-card" style="left:149px">
    <div class="photo" role="img" aria-label="Photo of colleagues in a meeting room" style="background:linear-gradient(135deg,#dfe3e6,#7b8a96)"></div>
    <div class="meta"><time>Augst 31, 2022</time><h4>Meridale Partner<br>Journey</h4>
    <div class="read-more">Read More<span class="ring"><svg width="6" height="8"><path d="M1 1l3 3-3 3" stroke="#e8873a" fill="none"/></svg></span></div></div>
  </article>
  <article class="insight-card featured" style="left:457px" role="img" aria-label="Photo of two colleagues working late at a laptop">
    <div class="meta"><time>Augst 31, 2022</time><h4>Meridale Partner<br>Journey</h4>
    <div class="read-more">Read More<span class="ring"><svg width="6" height="8"><path d="M1 1l3 3-3 3" stroke="#e8873a" fill="none"/></svg></span></div></div>
  </article>
  <article class="insight-card" style="left:766px">
    <div class="photo" role="img" aria-label="Photo of hands holding a tablet with data overlays" style="background:linear-gradient(135deg,#8ea5b8,#d5dde4)"></div>
    <div class="meta"><time>Augst 31, 2022</time><h4>Meridale Partner<br>Journey</h4>
    <div class="read-more">Read More<span class="ring"><svg width="6" height="8"><path d="M1 1l3 3-3 3" stroke="#e8873a" fill="none"/></svg></span></div></div>
  </article>
</section>

<section class="contact">
  <h2 class="heading contact-heading">Contact us to discuss<br>your business needs</h2>
  <div class="btn" style="left:131px;top:3302px;width:176px;padding-left:50px;padding-right:14px;font-family:'Poppins',sans-serif;font-weight:600;font-size:17px">01 555 0142<span class="dot"><svg width="18" height="18" viewBox="0 0 24 24"><path d="M6.6 10.8a15 15 0 0 0 6.6 6.6l2.2-2.2c.3-.3.7-.4 1-.2 1.1.4 2.3.6 3.6.6.6 0 1 .4 1 1V20c0 .6-.4 1-1 1A17 17 0 0 1 3 4c0-.6.4-1 1-1h3.5c.6 0 1 .4 1 1 0 1.3.2 2.5.6 3.6.1.3 0 .7-.2 1z" fill="#284a61"/></svg></span></div>
  <div class="btn" style="left:318px;top:3302px;width:177px">CONTACT US<span class="dot"><svg width="18" height="14"><rect x="1" y="1" width="16" height="12" rx="2" fill="none" stroke="#284a61" stroke-width="1.6"/><path d="M1 2l8 6 8-6" fill="none" stroke="#284a61" stroke-width="1.6"/></svg></span></div>
  <div class="abs" role="img" aria-label="Photo of a smiling consultant holding a tablet" style="left:663px;top:3177px;width:258px;height:331px;border-radius:120px 120px 0 0;background:linear-gradient(180deg,#c9a98b,#6a4b48 45%,#3b4a5c)"></div>
</section>

<footer class="site-footer">
  <div class="brand"><span class="mark"></span><span>Meridale<br>Partners</span></div>
  <div class="partner-badge"><span style="width:84px;background:#c74634"></span><span style="width:1px;height:28px;background:#fff"></span><span style="width:52px;background:rgba(255,255,255,.6)"></span></div>
  <div class="foot-col" style="left:329px"><h5>Sitemap</h5><ul><li class="bullet">Home</li><li class="bullet">About Us</li><li class="bullet">Services</li><li class="bullet">Contact Us</li></ul></div>
  <div class="foot-col" style="left:494px"><h5>Services</h5><ul><li class="bullet">Advise &amp; Architect</li><li class="bullet">Design &amp; Implement</li><li class="bullet">Optimse &amp; Manage</li></ul></div>
  <div class="foot-col" style="left:680px"><h5>Contact Us</h5>
    <ul class="contact-list">
      <li><svg width="16" height="20" viewBox="0 0 16 20"><path d="M8 0a7 7 0 0 0-7 7c0 5 7 13 7 13s7-8 7-13a7 7 0 0 0-7-7z" fill="#e8873a"/><circle cx="8" cy="7" r="2.6" fill="#284a61"/></svg><span>12 Harbour Lane, Dockside,<br>Dublin 4, D04 XY10</span></li>
      <li><svg width="16" height="16" viewBox="0 0 24 24"><path d="M6.6 10.8a15 15 0 0 0 6.6 6.6l2.2-2.2c.3-.3.7-.4 1-.2 1.1.4 2.3.6 3.6.6.6 0 1 .4 1 1V20c0 .6-.4 1-1 1A17 17 0 0 1 3 4c0-.6.4-1 1-1h3.5c.6 0 1 .4 1 1 0 1.3.2 2.5.6 3.6.1.3 0 .7-.2 1z" fill="#e8873a"/></svg><span>01 555 0142</span></li>
      <li><svg width="16" height="13"><rect x="0" y="0" width="16" height="13" rx="2" fill="#e8873a"/><path d="M1 1l7 6 7-6" fill="none" stroke="#284a61" stroke-width="1.4"/></svg><span>info@meridale-partners.example</span></li>
    </ul>
  </div>
  <div class="foot-col" style="left:955px"><h5>Follow Us</h5><div class="social"><span></span><span></span></div></div>
  <div class="foot-rule"></div>
  <div class="copyright">©MERIDALE PARTNERS &nbsp;- 2022 All rights reserved.</div>
</footer>

</body>
</html>
```